Tall Fern Roofing Business Card

Need a business card with the logo that was designed here

Contact Information for Business Card

Name, Title, Phone, Email, Website, Company name

```html
<!DOCTYPE html>
<html lang="en">
<head>
<meta charset="utf-8">
<title>Tall Fern Roofing Business Card</title>
<link rel="stylesheet" href="https://fonts.googleapis.com/css2?family=Montserrat:wght@400;500;700&display=swap">
<style>
  :root {
    --page-bg: #e9e4dc;
    --card-top: #f6f4f1;
    --card-bottom: #e6e2dc;
    --brand-blue: #245a9c;
    --band-blue: #2f5f9a;
    --band-deep: #1d4a86;
    --ink: #3a3c40;
    --rule-grey: #55585d;
  }
  html, body {
    margin: 0;
    width: 1200px;
    height: 897px;
    overflow: hidden;
    background: var(--page-bg);
    font-family: "Montserrat", sans-serif;
  }
  .card {
    position: absolute;
    left: 100px;
    top: 176px;
    width: 1000px;
    height: 545px;
    border-radius: 26px;
    overflow: hidden;
    background: linear-gradient(160deg, var(--card-top), var(--card-bottom));
    box-shadow: 0 10px 30px rgba(0,0,0,0.12);
  }
  .wave {
    position: absolute;
    left: 0;
    bottom: 0;
    width: 1000px;
    height: 545px;
  }
  .brand {
    position: absolute;
    left: 60px;
    top: 250px;
    width: 420px;
    display: flex;
    align-items: center;
    gap: 14px;
  }
  .brand-mark {
    width: 26px;
    height: 26px;
    background: var(--brand-blue);
    flex: none;
  }
  .brand-name {
    font-weight: 700;
    font-size: 34px;
    color: var(--brand-blue);
    white-space: nowrap;
  }
  .divider {
    position: absolute;
    left: 505px;
    top: 142px;
    width: 2px;
    height: 262px;
    background: var(--brand-blue);
  }
  .contact {
    position: absolute;
    left: 547px;
    top: 140px;
    color: var(--ink);
  }
  .person-name {
    margin: 0;
    font-weight: 700;
    font-size: 31px;
    letter-spacing: 1px;
    color: var(--brand-blue);
  }
  .person-title {
    margin: 2px 0 0;
    font-size: 20px;
    font-weight: 500;
    letter-spacing: 0.5px;
  }
  .details {
    list-style: none;
    margin: 26px 0 0;
    padding: 0;
  }
  .details li {
    display: flex;
    align-items: center;
    gap: 12px;
    font-size: 20px;
    font-weight: 500;
    letter-spacing: 0.5px;
    height: 37px;
  }
  .details svg { width: 17px; height: 17px; fill: var(--brand-blue); flex: none; }
  .address {
    margin: 18px 0 0;
    font-style: normal;
    font-size: 20px;
    font-weight: 500;
    letter-spacing: 0.5px;
    line-height: 30px;
  }
</style>
</head>
<body>
  <div class="card">
    <svg class="wave" viewBox="0 0 1000 545" aria-hidden="true">
      <path d="M0 420 C 300 470, 600 520, 1000 505 L 1000 545 L 0 545 Z" fill="var(--band-blue)"/>
      <path d="M420 500 C 650 515, 850 500, 1000 490 L 1000 498 C 850 508, 650 520, 420 500 Z" fill="var(--rule-grey)"/>
      <path d="M0 480 C 300 520, 600 545, 1000 515 L 1000 545 L 0 545 Z" fill="var(--band-deep)" opacity="0.45"/>
    </svg>

    <div class="brand">
      <span class="brand-mark"></span>
      <span class="brand-name">Tall Fern Roofing</span>
    </div>

    <div class="divider"></div>

    <div class="contact">
      <h1 class="person-name">DECLAN HARTWELL</h1>
      <p class="person-title">Managing Director</p>
      <ul class="details">
        <li>
          <svg viewBox="0 0 24 24"><path d="M6.6 10.8a15.1 15.1 0 0 0 6.6 6.6l2.2-2.2a1 1 0 0 1 1-.25 11.4 11.4 0 0 0 3.6.57 1 1 0 0 1 1 1V20a1 1 0 0 1-1 1A17 17 0 0 1 3 4a1 1 0 0 1 1-1h3.5a1 1 0 0 1 1 1c0 1.25.2 2.45.57 3.57a1 1 0 0 1-.25 1z"/></svg>
          0491 570 226
        </li>
        <li>
          <svg viewBox="0 0 24 24"><path d="M2 6h20v12H2z M2 6l10 7 10-7" fill="none" stroke="var(--brand-blue)" stroke-width="2.4"/></svg>
          info@tallfernroofing.com
        </li>
        <li>
          <svg viewBox="0 0 24 24"><circle cx="12" cy="12" r="9" fill="none" stroke="var(--brand-blue)" stroke-width="2.4"/><path d="M3 12h18M12 3c3 3 3 15 0 18M12 3c-3 3-3 15 0 18" fill="none" stroke="var(--brand-blue)" stroke-width="1.6"/></svg>
          www.tallfernroofing.com
        </li>
      </ul>
      <address class="address">1480 W Harbor Street<br>Mellows County Name 5230</address>
    </div>
  </div>
</body>
</html>
```